body therapist

I need to offer my services as a massage therapist at home, acclimating customer space aroma candles with music and everything else to bring comfort. 8 offer rituals like this: relaxing ritual, purifying ritual, ritual breast, facial and body cleansing ritual organic, ritual man, ritual feet, slimming ritual. Naraja handling colors, seawater, green, lavender

Target Market(s)

men and women, tired, stressed, looking for something new

Font styles to use
Decorative
Script

Colors
f37122
0493ce
abd037

Requirements
Must have
• detailing each massage
Nice to have
• simple and elegant

```html
<!DOCTYPE html>
<html lang="es">
<head>
<meta charset="utf-8">
<title>Serenia Spa – Rituales y Masajes</title>
<link href="https://fonts.googleapis.com/css2?family=Courier+Prime:wght@400;700&family=Raleway:wght@300;400;500&family=Indie+Flower&family=Yellowtail&display=swap" rel="stylesheet">
<style>
  :root{
    --backdrop:#3d3d3d;
    --paper:#ffffff;
    --lime:#abd037;
    --lime-bright:#b3d63b;
    --orchid:#c35ccc;
    --ink:#555555;
    --ink-soft:#7a7a7a;
    --panel:rgba(238,238,238,0.93);
    --tab:#e4e4e4;
  }
  *{box-sizing:border-box;margin:0;padding:0}
  html,body{width:1200px;height:1200px;overflow:hidden;background:var(--backdrop)}
  .spread{position:absolute;left:60px;top:220px;width:1080px;height:760px;display:flex;box-shadow:0 20px 50px rgba(0,0,0,.45)}
  .page{position:relative;width:540px;height:760px;background:var(--paper);overflow:hidden}
  .page--left::after{content:"";position:absolute;right:0;top:0;width:40px;height:100%;background:linear-gradient(to right,rgba(0,0,0,0),rgba(0,0,0,.12))}
  .page--right::after{content:"";position:absolute;left:0;top:0;width:40px;height:100%;background:linear-gradient(to left,rgba(0,0,0,0),rgba(0,0,0,.1))}
  .page svg.art{position:absolute;inset:0;width:540px;height:760px}
  .page-number{position:absolute;top:0;width:60px;height:30px;border-radius:0 0 30px 30px;background:var(--tab);color:var(--ink-soft);font:400 13px 'Raleway',sans-serif;text-align:center;line-height:22px;z-index:2}
  .page--left .page-number{left:240px}
  .page--right .page-number{left:80px}

  .rituals-panel{position:absolute;left:60px;top:250px;width:290px;height:470px;background:var(--panel);padding:34px 24px;z-index:2}
  .explore-title{font:700 48px/1 'Courier Prime',monospace;color:var(--orchid);letter-spacing:-1px;white-space:nowrap}
  .explore-sub{margin-top:14px;font:700 24px/1.05 'Courier Prime',monospace;color:var(--ink)}
  .ritual-intro{margin-top:22px;font:400 19px/1.3 'Indie Flower',cursive;color:var(--ink)}
  .ritual-list{list-style:none;font:400 18px/1.42 'Indie Flower',cursive;color:var(--ink);font-variant-ligatures:none}
  .ritual-list li::before{content:"";display:inline-block;width:6px;height:6px;background:#cfcfcf;margin-right:9px;vertical-align:middle}

  .brand-name{position:absolute;left:190px;top:28px;font:400 50px/1 'Yellowtail',cursive;color:var(--lime);z-index:2}
  .intro{position:absolute;left:40px;top:96px;width:460px;font:400 11px/1.45 'Raleway',sans-serif;color:var(--ink-soft);text-align:justify;z-index:2}

  .massage-panel{position:absolute;left:280px;top:170px;width:220px;height:390px;background:var(--panel);padding:26px 20px;z-index:2}
  .massage-title{font:700 34px/1 'Courier Prime',monospace;color:var(--orchid);letter-spacing:1px}
  .massage-list{list-style:none;margin-top:18px;font:400 13px/1.3 'Raleway',sans-serif;color:var(--ink);text-transform:uppercase}
  .massage-list li{position:relative;padding-left:18px;margin-bottom:12px}
  .massage-list li::before{content:"";position:absolute;left:0;top:4px;width:7px;height:7px;background:var(--orchid)}
  .duration{position:absolute;left:330px;top:500px;width:200px;height:38px;background:var(--lime-bright);color:#fff;font:400 14px/38px 'Raleway',sans-serif;text-align:center;text-transform:uppercase;z-index:3}
</style>
</head>
<body>
<main class="spread">
  <section class="page page--left">
    <svg class="art" viewBox="0 0 540 760">
      <defs>
        <linearGradient id="topPhoto" x1="0" y1="0" x2="1" y2="0">
          <stop offset="0" stop-color="#fafbf7"/><stop offset=".45" stop-color="#e6eed5"/><stop offset="1" stop-color="#eee4f3"/>
        </linearGradient>
        <linearGradient id="stonePhoto" x1="0" y1="0" x2="1" y2="1">
          <stop offset="0" stop-color="#a3a2a8"/><stop offset=".6" stop-color="#8d8c94"/><stop offset="1" stop-color="#7ea56a"/>
        </linearGradient>
      </defs>
      <rect x="0" y="30" width="540" height="180" fill="url(#topPhoto)" role="img" aria-label="Foto de bambú de la suerte, orquídeas lilas y una piedra negra de relajación"/>
      <path d="M40 330 Q300 330 540 250 L540 760 L40 760 Z" fill="var(--lime-bright)"/>
      <path d="M200 760 L200 420 Q270 310 540 300 L540 760 Z" fill="url(#stonePhoto)" role="img" aria-label="Foto de una escultura de piedra zen entre hojas verdes"/>
    </svg>
    <div class="page-number">2</div>
    <div class="rituals-panel">
      <h2 class="explore-title">Explorar</h2>
      <p class="explore-sub">Nuevos Rituales de relajación</p>
      <p class="ritual-intro">8 rituales así:</p>
      <ul class="ritual-list">
        <li>ritual relajante,</li>
        <li>ritual purificante,</li>
        <li>ritual mamá,</li>
        <li>ritual limpieza orgánica</li>
        <li>facial y corporal,</li>
        <li>ritual hombre,</li>
        <li>ritual pies,</li>
        <li>ritual adelgazante.</li>
      </ul>
    </div>
  </section>

  <section class="page page--right">
    <svg class="art" viewBox="0 0 540 760">
      <defs>
        <linearGradient id="massagePhoto" x1="0" y1="0" x2="1" y2="1">
          <stop offset="0" stop-color="#f4dca6"/><stop offset=".5" stop-color="#efc2aa"/><stop offset="1" stop-color="#f8eee6"/>
        </linearGradient>
      </defs>
      <path d="M60 250 L540 190 L540 560 L60 560 Z" fill="var(--lime-bright)"/>
      <rect x="60" y="280" width="430" height="480" fill="url(#massagePhoto)" role="img" aria-label="Foto de una mujer recibiendo un masaje relajante en la espalda"/>
    </svg>
    <div class="page-number">3</div>
    <h1 class="brand-name">Serenia Spa</h1>
    <p class="intro">Un espacio para tu CUERPO, MENTE Y ESPÍRITU... SERENIA es una empresa dedicada a brindar bienestar al ser sin salir de casa, transformando tu espacio con innovadoras técnicas de masajes, terapias y rituales para así llegar al máximo nivel de relajación del zen.</p>
    <div class="massage-panel">
      <h2 class="massage-title">MASAJES</h2>
      <ul class="massage-list">
        <li>Masaje zen con</li>
        <li>Piedras sabay</li>
        <li>Masaje aromático</li>
        <li>Masaje a cuatro manos</li>
        <li>Masaje relajante</li>
        <li>Masaje reductor</li>
      </ul>
    </div>
    <div class="duration">De 60-90 minutes</div>
  </section>
</main>
</body>
</html>
```